Pages That Pay Dividends - book cover (front panel only)

I want a book cover (for print and ebook) in a distinctive, quirky style that can be repurposed for podcast artwork too. Full brief supplied.
The book is a practical, accessible handbook for anyone thinking about writing a book to build their business, with a wide range of tips and techniques to help plan, write, publishing and promote a book that’s integrated with your platform and works to build your reputation, network and credibility from day 1.
The target audience is experts in business, particularly owners of SMEs with an established online and offline platform (eg speaking, training, consulting) who want to add a book to take their business to the next level.
I want the design to be strong and distinctive, slightly quirky without being gimmicky, with the focus on typography.

Target Market(s)

Those writing a book based on their expertise to build their business

Industry/Entity Type

Publishing Company

Font styles to use
Serif
Sans Serif
Decorative

Colors

Designer to choose colors to be used in the design.

Requirements
Must have
• Commercially appealing book cover design, with application files and copyright supplied, front panel only, 5.5 x 8.5 inch format. Must work at both full size and thumbnail.
Nice to have
• A distinctive style that could be applied across other products in my portfolio.

```html
<!DOCTYPE html>
<html lang="en">
<head>
<meta charset="utf-8">
<title>Pages That Pay Dividends — Book Cover</title>
<link rel="stylesheet" href="https://fonts.googleapis.com/css2?family=Bebas+Neue&family=Caveat:wght@500&display=swap">
<style>
  :root {
    --sky: #1f6d9c;
    --sky-deep: #1b5e88;
    --accent: #f5ae47;
    --white: #ffffff;
    --author: #5d5e60;
    --pen-dark: #55575a;
    --pen-gold: #efac48;
  }
  html, body {
    margin: 0;
    padding: 0;
    overflow: hidden;
    background: #ffffff;
  }
  .cover {
    position: relative;
    width: 787px;
    height: 1200px;
    overflow: hidden;
    background: var(--sky);
  }
  .cover__scene {
    position: absolute;
    left: 0;
    top: 680px;
    width: 787px;
    height: 520px;
    background: linear-gradient(180deg, var(--sky) 0%, var(--sky-deep) 12%, #c9dbe7 40%, var(--white) 62%, var(--white) 100%);
  }
  .cover__pen {
    position: absolute;
    left: 556px;
    top: 50px;
    width: 130px;
    height: 720px;
    background: linear-gradient(180deg, var(--pen-gold) 0%, #b48847 30%, var(--pen-dark) 55%, #8a7a5a 80%, #eef3f6 100%);
  }
  .cover__title {
    position: absolute;
    left: 50px;
    top: 38px;
    margin: 0;
    font-family: "Bebas Neue", "Oswald", sans-serif;
    font-weight: 400;
    font-size: 124px;
    line-height: 123px;
    letter-spacing: 3px;
    text-transform: uppercase;
  }
  .cover__title span { display: block; }
  .cover__title .title-accent { color: var(--accent); }
  .cover__title .title-strong { color: var(--white); }
  .cover__subtitle {
    position: absolute;
    left: 79px;
    top: 448px;
    margin: 0;
    font-family: "Caveat", cursive;
    font-weight: 500;
    font-size: 47px;
    line-height: 51px;
    color: var(--accent);
  }
  .cover__subtitle span { display: block; }
  .cover__author {
    position: absolute;
    left: 0;
    right: 0;
    top: 1044px;
    margin: 0;
    text-align: center;
    font-family: "Bebas Neue", "Oswald", sans-serif;
    font-weight: 400;
    font-size: 160px;
    line-height: 160px;
    letter-spacing: 5px;
    color: var(--author);
    text-transform: uppercase;
  }
</style>
</head>
<body>
  <main class="cover">
    <div class="cover__scene" role="img" aria-label="Illustration of billowing white clouds rising over a darker blue hill, with a faint line chart across the sky"></div>

    <div class="cover__pen" role="img" aria-label="Illustration of a gold and charcoal fountain pen launching upward like a rocket, trailing white exhaust"></div>

    <h1 class="cover__title">
      <span class="title-accent">Pages That</span>
      <span class="title-accent">Pay</span>
      <span class="title-strong">Dividends</span>
    </h1>

    <p class="cover__subtitle">
      <span>Clever ways to plan and</span>
      <span>write a book that works</span>
      <span>harder for your business</span>
    </p>

    <p class="cover__author">Maren Holt</p>
  </main>
</body>
</html>
```